Website for International Non-Profit for Birth Parent Searching

LumaKin is a 501(c)(3) non-profit organization that helps Chinese adoptees search and reunite with birth families who were separated due the One Child Policy in China. We want to create a website that can link to an information database that allows website users to easily access information around search ads in an organized way; help connect families to professional searchers; provide resources for community support for adoptees and their families as they embark on a personal and emotional journey of finding birth family through support groups on social media and consultation/education on the searching process; and provide the opportunity for the adoptive community to give back through donations and volunteer opportunities. The final design should foster a sense of community and be easy navigable to access the multiple resources we provide to help families search for each other. We would like to see designs with red/black/white color schemes that are gentle, inviting, and family friendly to viewers. We would like to see some design layouts with Chinese themes, if possible.

```html
<!DOCTYPE html>
<html lang="en">
<head>
<meta charset="utf-8">
<title>LumaKin — Birth Family Search</title>
<link href="https://fonts.googleapis.com/css2?family=Montserrat:wght@600;700&family=Roboto:wght@400;500;700&display=swap" rel="stylesheet">
<style>
:root{
  --red:#e31b1b;
  --ink:#1b1b1b;
  --text:#6f6f6f;
  --black:#111;
  --footer:#1d1d1d;
  --soft:#f2f2f2;
  --white:#fff;
  --line:#dadada;
}
*{box-sizing:border-box;margin:0;padding:0}
html,body{width:1200px;height:3694px;overflow:hidden}
body{font-family:"Roboto",sans-serif;color:var(--ink);background:var(--white);position:relative}
.abs{position:absolute}
h2.section-title{font-family:"Montserrat",sans-serif;font-weight:700;font-size:35px;text-transform:uppercase;color:var(--ink)}
h2.section-title span{color:var(--red)}
.btn{display:inline-block;background:var(--red);color:var(--white);font-weight:700;font-size:15px;text-transform:uppercase;text-align:center}

/* top bar */
.topbar{top:0;left:0;width:1200px;height:48px;background:var(--black);color:var(--white);font-size:15px;font-weight:500}
.topbar .contact-line{left:112px;top:14px;display:flex;align-items:center;gap:10px}
.topbar .social{right:112px;top:8px;display:flex;gap:10px}
.topbar .social span{width:32px;height:32px;background:#2e2e2e;display:block}
.topbar .social span i{display:block;width:10px;height:10px;background:var(--white);margin:11px}

/* nav */
.nav{top:48px;left:0;width:1200px;height:89px;background:var(--white)}
.logo{font-family:"Montserrat",sans-serif;font-weight:700;font-size:34px;letter-spacing:1px}
.nav .logo{left:112px;top:22px;color:var(--red)}
.nav ul{list-style:none;left:349px;top:35px;display:flex;gap:27px;font-size:15px;font-weight:500}
.nav ul li:first-child{color:var(--red)}
.nav .btn{left:956px;top:21px;width:132px;height:46px;line-height:46px}

/* hero */
.hero{top:137px;left:0;width:1200px;height:600px;background:linear-gradient(100deg,#d9cbb6 0%,#c9a58c 40%,#b78872 60%,#2d7b7c 85%,#c9b49a 100%)}
.hero-copy{left:112px;top:210px}
.hero h1{font-family:"Montserrat",sans-serif;font-size:34px;font-weight:700;text-transform:uppercase}
.hero h1 span{color:var(--red)}
.hero p{font-size:17px;font-weight:500;line-height:28px;margin-top:18px;width:390px}
.hero .btn{margin-top:22px;width:140px;height:46px;line-height:46px}
.dots{left:569px;top:568px;display:flex;gap:6px}
.dots i{width:11px;height:11px;border:1.5px solid var(--white);display:block}
.dots i.on{background:var(--red)}

/* about */
.about{top:737px;left:0;width:1200px;height:572px}
.about .section-title{left:112px;top:105px}
.about .copy{left:112px;top:165px;width:486px;font-size:15px;line-height:25px;color:var(--text);text-align:justify}
.about .copy p+p{margin-top:18px}
.about .btn{left:112px;top:413px;width:132px;height:46px;line-height:46px}
.about .frame{left:656px;top:95px;width:433px;height:383px;background:var(--white);box-shadow:0 2px 10px rgba(0,0,0,.18);padding:6px}
.about .frame div{width:100%;height:100%;background:linear-gradient(160deg,#e9ede6,#c5d59b 45%,#e67a8c 70%,#9a9582)}

/* organized */
.organized{top:1309px;left:0;width:1200px;height:446px;background:var(--soft)}
.organized .section-title{left:0;width:1200px;text-align:center;top:52px}
.card{top:139px;width:316px;height:248px;background:var(--white);box-shadow:0 1px 6px rgba(0,0,0,.12);text-align:center;color:var(--text);font-size:14.5px;line-height:22px}
.card .icon{width:62px;height:62px;margin:30px auto 0;border:3px solid var(--red);border-radius:50%}
.card p{position:absolute;left:18px;right:18px;bottom:0;height:150px;display:flex;align-items:center;justify-content:center}

/* testimonials */
.testimonials{top:1755px;left:0;width:1200px;height:383px;background:linear-gradient(90deg,#e01e1e,#e52a2a 50%,#df1c1c);color:var(--white)}
.testimonials .section-title{color:var(--white);left:0;width:1200px;text-align:center;top:70px}
.quote{top:180px;width:470px}
.quote .avatar{position:absolute;left:0;top:2px;width:120px;height:120px;border-radius:50%;border:3px solid var(--white);background:linear-gradient(180deg,#8fa497,#2c3446)}
.quote .q{position:absolute;left:143px;top:0;font-family:"Montserrat",sans-serif;font-size:30px;line-height:30px;color:rgba(255,255,255,.55)}
.quote p{position:absolute;left:173px;top:4px;width:295px;font-size:15px;line-height:24px}
.quote h4{position:absolute;left:173px;top:93px;font-size:15px;font-weight:700;text-transform:uppercase}
.quote span{position:absolute;left:173px;top:115px;font-size:15px}
.arrow{top:177px}

/* blog */
.blog{top:2138px;left:0;width:1200px;height:727px}
.blog .section-title{left:0;width:1200px;text-align:center;top:87px}
.post{background:var(--white);box-shadow:0 1px 8px rgba(0,0,0,.14)}
.post .ph{position:absolute;background:linear-gradient(150deg,#efeae3,#d8ccbd 50%,#9aa2b8)}
.post h3{position:absolute;font-size:18.5px;font-weight:700;line-height:23px}
.post p{position:absolute;font-size:13.5px;line-height:19px;color:var(--text)}
.post .more{position:absolute;color:var(--red);font-weight:700;font-size:14px;display:flex;align-items:center;gap:14px}
.post .date{position:absolute;font-size:13px;color:var(--text);display:flex;align-items:center;gap:6px}
.big{left:112px;top:165px;width:466px;height:469px}
.big .ph{left:9px;top:8px;width:448px;height:324px}
.big h3{left:19px;top:348px}
.big p{left:19px;top:380px;width:428px}
.big .more{left:19px;top:431px}
.big .date{right:19px;top:432px}
.small{left:598px;width:491px;height:143px}
.small .ph{left:10px;top:9px;width:148px;height:125px}
.small h3{left:172px;top:12px;width:310px}
.small p{left:172px;top:60px;width:310px}
.small .more{left:172px;top:109px}
.small .date{right:14px;top:110px}

/* contact */
.contact{top:2865px;left:0;width:1200px;height:456px;background:var(--soft)}
.contact .section-title{left:0;width:1200px;text-align:center;top:38px}
.field{height:44px;background:var(--white);border:1px solid var(--line);font-size:15px;color:#777;padding:14px 15px}
.field.select{display:flex;justify-content:space-between}
.contact .submit{left:202px;top:370px;width:796px;height:43px;line-height:43px;font-size:15px}

/* footer */
.footer{top:3321px;left:0;width:1200px;height:373px;background:var(--footer);color:var(--white)}
.footer .logo{left:110px;top:62px;font-size:40px;color:var(--red)}
.footer h5{font-size:19px;font-weight:500}
.footer h6{font-size:14px;font-weight:700}
.footer .rule{display:block;width:30px;height:2px;background:var(--red);margin-top:10px}
.footer ul{list-style:none;font-size:15px;line-height:24px;margin-top:18px}
.follow li{display:flex;align-items:center;gap:22px;line-height:29px}
.follow li i{width:12px;height:12px;background:var(--white);display:block}
.contact-list li{display:flex;gap:20px;line-height:24px;margin-bottom:8px}
.contact-list svg{flex:none;margin-top:5px}
.bottom-nav{left:430px;top:249px;width:659px;height:56px;border-top:1px solid #555;border-bottom:1px solid #555;display:flex;justify-content:center;align-items:center;gap:14px;font-size:15px;font-weight:700}
.copyright{left:430px;top:334px;width:659px;font-size:12px;padding-left:36px}
</style>
</head>
<body>

<header class="topbar abs">
  <div class="contact-line abs">
    <svg width="13" height="13" viewBox="0 0 24 24"><path fill="#e31b1b" d="M6.6 10.8a15 15 0 0 0 6.6 6.6l2.2-2.2c.3-.3.7-.4 1-.2 1.1.4 2.3.6 3.6.6.6 0 1 .4 1 1V20c0 .6-.4 1-1 1A17 17 0 0 1 3 4c0-.6.4-1 1-1h3.5c.6 0 1 .4 1 1 0 1.3.2 2.5.6 3.6.1.3 0 .7-.2 1z"/></svg>
    <span>(555) 014 2368</span>
    <span style="margin:0 12px">|</span>
    <svg width="15" height="12" viewBox="0 0 24 18"><rect x="1" y="1" width="22" height="16" rx="2" fill="none" stroke="#e31b1b" stroke-width="2"/><path d="M1 2l11 8 11-8" fill="none" stroke="#e31b1b" stroke-width="2"/></svg>
    <span>info@lumakin.org</span>
  </div>
  <div class="social abs"><span><i></i></span><span><i></i></span><span><i></i></span></div>
</header>

<nav class="nav abs">
  <div class="logo abs">LUMAKIN</div>
  <ul class="abs"><li>HOME</li><li>ABOUT US</li><li>ORGANIZE WE</li><li>REVIEWS</li><li>BLOG</li><li>CONTACT US</li></ul>
  <span class="btn abs">SERCH ADD</span>
</nav>

<section class="hero abs" role="img" aria-label="Photo of a smiling family with a baby sitting together at home">
  <div class="hero-copy abs">
    <h1><span>Welcome to</span> LumaKin</h1>
    <p>Lorem ipsum dolor sit amet, consectetur adipis cing elit, sed do eiusmod tempor</p>
    <span class="btn">Connect Now</span>
  </div>
  <div class="dots abs"><i></i><i></i><i class="on"></i><i></i></div>
</section>

<section class="about abs">
  <h2 class="section-title abs"><span>About</span> Us</h2>
  <div class="copy abs">
    <p>Lorem ipsum dolor sit amet, consectetur adipiscing elit, sed do eiusmod tempor incididunt ut labore et dolore magna aliqua. Ut enim ad minim veniam, quis nostrud exercitation ullamco laboris nisi ut aliquip ex ea commodo consequat. Duis aute irure dolor in reprehenderit in voluptate velit esse cillum dolore eu fugiat.</p>
    <p>Lorem ipsum dolor sit amet, consectetur adipiscing elit, sed do eiusmod tempor incididunt ut labore et dolore magna aliqua. Ut enim ad minim veniam, quis nostrud dolore.</p>
  </div>
  <span class="btn abs">Learn More</span>
  <div class="frame abs"><div role="img" aria-label="Photo of a family riding bicycles in a sunny park"></div></div>
</section>

<section class="organized abs">
  <h2 class="section-title abs"><span>We</span> Organized</h2>
  <div class="card abs" style="left:112px"><div class="icon" role="img" aria-label="Baby icon"></div><p>Help connect families to professional searchers</p></div>
  <div class="card abs" style="left:442px"><div class="icon" role="img" aria-label="Two people icon"></div><p>Provide the opportunity for the adoptive community to give back through donations and volunteer opportunities.</p></div>
  <div class="card abs" style="left:772px"><div class="icon" role="img" aria-label="Parent holding child icon"></div><p>Provide resources for community support for adoptees and their families as they embark on a personal and emotional journey of finding birth family through support groups on social media</p></div>
</section>

<section class="testimonials abs">
  <h2 class="section-title abs">Testimonials</h2>
  <svg class="arrow abs" style="left:24px" width="18" height="40" viewBox="0 0 18 40"><path d="M16 2L3 20l13 18" fill="none" stroke="rgba(255,255,255,.6)" stroke-width="3"/></svg>
  <div class="quote abs" style="left:112px">
    <div class="avatar" role="img" aria-label="Portrait photo of a young man"></div>
    <span class="q">“</span>
    <p>Lorem ipsum dolor sit amet, consectetur a ipis cing elit, sed do eiusmod tempor incididunt ut labore et dol.</p>
    <h4>Daniel Wei</h4><span>China</span>
  </div>
  <div class="quote abs" style="left:628px">
    <div class="avatar" role="img" aria-label="Portrait photo of a young woman"></div>
    <span class="q">“</span>
    <p>Lorem ipsum dolor sit amet, consectetur a ipis cing elit, sed do eiusmod tempor incididunt ut labore et dol.</p>
    <h4>Daniel Wei</h4><span>China</span>
  </div>
  <svg class="arrow abs" style="left:1158px" width="18" height="40" viewBox="0 0 18 40"><path d="M2 2l13 18L2 38" fill="none" stroke="#fff" stroke-width="3"/></svg>
</section>

<section class="blog abs">
  <h2 class="section-title abs"><span>Latest</span> Blog</h2>
  <article class="post big abs">
    <div class="ph" role="img" aria-label="Photo of a family of three sitting on a sofa"></div>
    <h3>The standard Lorem Ipsum passage, used since</h3>
    <p>Lorem ipsum dolor sit amet, consectetur adipiscing elit, sed do eiu smod tempor incididunt ut labore</p>
    <span class="more">Read More <svg width="13" height="13" viewBox="0 0 14 14"><circle cx="7" cy="7" r="6" fill="none" stroke="#e31b1b" stroke-width="1.6"/><path d="M4 7h6M7.5 4.5L10 7 7.5 9.5" fill="none" stroke="#e31b1b" stroke-width="1.6"/></svg></span>
    <span class="date"><svg width="12" height="12" viewBox="0 0 12 12"><rect x="1" y="2" width="10" height="9" fill="none" stroke="#e31b1b" stroke-width="1.4"/><path d="M1 5h10" stroke="#e31b1b" stroke-width="1.4"/></svg>23 Mar 2021</span>
  </article>
  <article class="post small abs" style="top:165px">
    <div class="ph" role="img" aria-label="Photo of two smiling girls"></div>
    <h3>The standard Lorem Ipsum passage used since</h3>
    <p>Lorem ipsum dolor sit amet, consectetur adipisi iscing elit, sed do eiusmod tempor</p>
    <span class="more">Read More <svg width="13" height="13" viewBox="0 0 14 14"><circle cx="7" cy="7" r="6" fill="none" stroke="#e31b1b" stroke-width="1.6"/><path d="M4 7h6M7.5 4.5L10 7 7.5 9.5" fill="none" stroke="#e31b1b" stroke-width="1.6"/></svg></span>
    <span class="date"><svg width="12" height="12" viewBox="0 0 12 12"><rect x="1" y="2" width="10" height="9" fill="none" stroke="#e31b1b" stroke-width="1.4"/><path d="M1 5h10" stroke="#e31b1b" stroke-width="1.4"/></svg>23 Mar 2021</span>
  </article>
  <article class="post small abs" style="top:327px">
    <div class="ph" role="img" aria-label="Photo of a mother and baby at home"></div>
    <h3>The standard Lorem Ipsum passage used since</h3>
    <p>Lorem ipsum dolor sit amet, consectetur adipisi iscing elit, sed do eiusmod tempor</p>
    <span class="more">Read More <svg width="13" height="13" viewBox="0 0 14 14"><circle cx="7" cy="7" r="6" fill="none" stroke="#e31b1b" stroke-width="1.6"/><path d="M4 7h6M7.5 4.5L10 7 7.5 9.5" fill="none" stroke="#e31b1b" stroke-width="1.6"/></svg></span>
    <span class="date"><svg width="12" height="12" viewBox="0 0 12 12"><rect x="1" y="2" width="10" height="9" fill="none" stroke="#e31b1b" stroke-width="1.4"/><path d="M1 5h10" stroke="#e31b1b" stroke-width="1.4"/></svg>23 Mar 2021</span>
  </article>
  <article class="post small abs" style="top:489px">
    <div class="ph" role="img" aria-label="Photo of a family celebrating outdoors"></div>
    <h3>The standard Lorem Ipsum passage used since</h3>
    <p>Lorem ipsum dolor sit amet, consectetur adipisi iscing elit, sed do eiusmod tempor</p>
    <span class="more">Read More <svg width="13" height="13" viewBox="0 0 14 14"><circle cx="7" cy="7" r="6" fill="none" stroke="#e31b1b" stroke-width="1.6"/><path d="M4 7h6M7.5 4.5L10 7 7.5 9.5" fill="none" stroke="#e31b1b" stroke-width="1.6"/></svg></span>
    <span class="date"><svg width="12" height="12" viewBox="0 0 12 12"><rect x="1" y="2" width="10" height="9" fill="none" stroke="#e31b1b" stroke-width="1.4"/><path d="M1 5h10" stroke="#e31b1b" stroke-width="1.4"/></svg>23 Mar 2021</span>
  </article>
</section>

<section class="contact abs">
  <h2 class="section-title abs"><span>Contact</span> Us</h2>
  <div class="field abs" style="left:202px;top:108px;width:394px">First Name</div>
  <div class="field abs" style="left:604px;top:108px;width:394px">Last Name</div>
  <div class="field abs" style="left:202px;top:162px;width:394px">Email</div>
  <div class="field abs" style="left:604px;top:162px;width:394px">Phone Number</div>
  <div class="field abs" style="left:202px;top:216px;width:394px">Zip Code</div>
  <div class="field select abs" style="left:604px;top:216px;width:394px"><span>I'm Interested In</span><svg width="10" height="10" viewBox="0 0 10 10"><path d="M2 3.5l3 3 3-3" fill="none" stroke="#777" stroke-width="1.3"/></svg></div>
  <div class="field abs" style="left:202px;top:270px;width:796px;height:90px">Comments</div>
  <span class="btn submit abs">Contact</span>
</section>

<footer class="footer abs">
  <div class="logo abs">LUMAKIN</div>
  <div class="abs" style="left:110px;top:162px">
    <h6>Follow Us:</h6><span class="rule"></span>
    <ul class="follow"><li><i></i>Photo Channel</li><li><i></i>Community Page</li><li><i></i>Updates Feed</li></ul>
  </div>
  <div class="abs" style="left:447px;top:50px">
    <h5>About Us</h5><span class="rule"></span>
    <ul><li>Site Map</li><li>Terms of Use</li><li>Privacy Policy</li></ul>
  </div>
  <div class="abs" style="left:638px;top:50px">
    <h5>Top Links</h5><span class="rule"></span>
    <ul><li>Adoption Centre</li><li>Open Adoption</li><li>Adoptive Family</li></ul>
  </div>
  <div class="abs" style="left:892px;top:50px">
    <h5>Contact Us</h5><span class="rule"></span>
    <ul class="contact-list">
      <li><svg width="12" height="14" viewBox="0 0 12 16"><path d="M6 0a6 6 0 0 0-6 6c0 4.5 6 10 6 10s6-5.5 6-10a6 6 0 0 0-6-6zm0 8.5A2.5 2.5 0 1 1 6 3.5a2.5 2.5 0 0 1 0 5z" fill="#fff"/></svg><span>2710 Lotus Lane, Hangzhou<br>China</span></li>
      <li><svg width="13" height="13" viewBox="0 0 24 24"><path fill="#fff" d="M6.6 10.8a15 15 0 0 0 6.6 6.6l2.2-2.2c.3-.3.7-.4 1-.2 1.1.4 2.3.6 3.6.6.6 0 1 .4 1 1V20c0 .6-.4 1-1 1A17 17 0 0 1 3 4c0-.6.4-1 1-1h3.5c.6 0 1 .4 1 1 0 1.3.2 2.5.6 3.6.1.3 0 .7-.2 1z"/></svg><span>(555) 014 2368</span></li>
      <li><svg width="14" height="11" viewBox="0 0 24 18"><rect x="1" y="1" width="22" height="16" rx="2" fill="none" stroke="#fff" stroke-width="2"/><path d="M1 2l11 8 11-8" fill="none" stroke="#fff" stroke-width="2"/></svg><span>info@lumakin.org</span></li>
    </ul>
  </div>
  <div class="bottom-nav abs"><span>HOME</span>|<span>ABOUT US</span>|<span>ORGANIZE WE</span>|<span>REVIEWS</span>|<span>BLOG</span>|<span>CONTACT US</span></div>
  <div class="copyright abs">Copyrights 2021 LUMAKIN. All Rights Reserved</div>
</footer>

</body>
</html>
```